Pull Up Banner - Recruitment Company

We would like a design for a pull up banner.

For context: we are a recruitment business. We specialise in helping people in healthcare industry to find jobs in Australia.

I have come up with several ideas and text for the banner. Feel free to use the following as you see appropriate:

- Our logo (see attached)
- 'Healthcare Recruitment Agency'
- Some sort of imagine / cartoon of medical professionals (ie. doctor, nurse, physiotherapist, speech pathologist). A cartoon is more friendly than committing to a photo
- 'Empowering your next career move'
- 'Discover tailored opportunities based on your career preferences'
- Dot points (allied health, nursing, medical imaging)
- Contact info at the bottom including our website (www.quellastaffing.com.au, our Instagram handle @quellastaffing, Mobile: XXXX XXX XXX. The title section for contact information could be 'Get in touch:'

Feel free to submit a couple of designs and we can merge aspects that look good on your designs and find the perfect fit.
Thank you
Updates

Hello,

Thank you for your initial submissions to this project. I appreciate the time you've invested.

After reviewing the first attempt, I'd like to share some feedback and initial observations:

- Professionalism and engagement: Is the overall appearance of the banner professional? It's crucial that we have a high-quality design as this will represent our business.

- Image selection: The image (whether cartoon or real people) appears quite generic. Please consider submitting the banner with a few different photos in the middle for us to choose from. Ensure the image is a good fit and not simply a generic stock photo.

- Contact section: Kindly remove the phone number; we no longer wish to include it on the banner. Instead, please include our website (www.quellastaffing.com.au) and Instagram handle (@quellastaffing).

- Color scheme: White, black, and red/pink are preferred, or alternatively, blue. However, please avoid incorporating too many different colors as it may detract from the professional appearance.

We will be printing the design on a banner and require it to look professional and engaging.

Thank you once again for your submissions. I hope the feedback provided above is helpful.

Warm regards,

Target Market(s)

Allied Health Australia

Font styles to use
Serif

Colors
0054AA
0677BA
7BADD7
CADEEF
E8F1F8
0094D4
00A9DD
6FCCEA
C7EBF8
E9F6FB
EB3D1F
EC4F4E
F09395
F8D3D4
FCEDEE

```html
<!DOCTYPE html>
<html lang="en">
<head>
<meta charset="utf-8">
<title>Quella Staffing – Pull Up Banner</title>
<link href="https://fonts.googleapis.com/css2?family=League+Spartan:wght@300;700;800&family=Poppins:wght@400;500;600;700&display=swap" rel="stylesheet">
<style>
  :root{
    --navy:#0a1485;
    --navy-deep:#0b1060;
    --royal:#3242d8;
    --sky:#6e9ef4;
    --accent:#1f86ec;
    --ink:#262626;
    --paper:#ffffff;
    --lilac:#c77ce0;
  }
  *{margin:0;padding:0;box-sizing:border-box}
  html,body{width:1200px;height:2400px;overflow:hidden;background:var(--paper)}
  .banner{position:relative;width:1200px;height:2400px;overflow:hidden;background:var(--navy);font-family:"Poppins",sans-serif}
  .banner-bg{position:absolute;inset:0}
  .brand{position:absolute;top:110px;left:0;width:100%;text-align:center;color:var(--paper);
    font-family:"League Spartan",sans-serif;font-weight:700;font-size:96px;letter-spacing:10px;line-height:1}
  .headline{position:absolute;top:300px;left:0;width:100%;text-align:center;font-family:"League Spartan",sans-serif;font-weight:800;line-height:.92;text-transform:uppercase}
  .headline .lead{display:block;color:var(--sky);font-size:112px}
  .headline .main{display:block;color:var(--paper);font-size:146px;letter-spacing:-2px}
  .scene{position:absolute;left:110px;top:700px;width:1000px;height:840px;border-radius:40px;
    background:radial-gradient(ellipse at 50% 50%, rgba(214,150,235,.55), rgba(90,110,230,.25) 60%, rgba(50,66,216,0) 80%)}
  .tagline{position:absolute;top:1655px;left:0;width:100%;text-align:center;color:var(--ink);font-family:"League Spartan",sans-serif;line-height:.95}
  .tagline .light{display:block;font-weight:300;font-size:84px}
  .tagline .bold{display:block;font-weight:800;font-size:84px}
  .discover{position:absolute;top:1808px;left:0;width:100%;text-align:center;color:var(--accent);font-weight:600;font-size:44px;letter-spacing:22px;padding-left:22px}
  .intro{position:absolute;top:1866px;left:0;width:100%;text-align:center;color:var(--ink);font-weight:600;font-size:46px;line-height:1.2;letter-spacing:-.5px}
  .sectors{position:absolute;top:1990px;left:70px;width:1060px;height:150px;display:flex;justify-content:center}
  .sector{display:flex;flex-direction:column;align-items:center;justify-content:flex-end;padding:0 48px;color:var(--ink);font-weight:500;font-size:38px}
  .sector+.sector{border-left:3px solid #cfcfcf}
  .sector svg{width:64px;height:64px;margin-bottom:14px}
  .web{position:absolute;top:2162px;left:115px;width:985px;height:100px;border-radius:22px;background:var(--ink);color:var(--paper);
    display:flex;align-items:center;justify-content:center;font-weight:700;font-size:48px;letter-spacing:3px}
  .social{position:absolute;top:2275px;left:0;width:100%;display:flex;align-items:center;justify-content:center;gap:14px;color:var(--ink);font-size:46px}
  .social .light{font-weight:400;color:#3a3a3a}
  .social .dot{width:34px;height:34px;border-radius:50%;background:#ec4f4e}
  .social .handle{font-weight:500}
</style>
</head>
<body>
<main class="banner">
  <svg class="banner-bg" width="1200" height="2400" viewBox="0 0 1200 2400" aria-hidden="true">
    <polygon points="0,820 1200,560 1200,2400 0,2400" fill="#0b1060"/>
    <polygon points="0,1300 1200,820 1200,1800 0,1800" fill="#3242d8"/>
    <polygon points="0,1400 1200,1000 1200,1080 0,1480" fill="#2a36c4"/>
    <polygon points="0,1660 1200,1560 1200,2400 0,2400" fill="#ffffff"/>
  </svg>

  <div class="brand">QUELLA STAFFING</div>

  <h1 class="headline">
    <span class="lead">Healthcare</span>
    <span class="main">Recruitment</span>
    <span class="main">Agency</span>
  </h1>

  <div class="scene" role="img" aria-label="Illustration of a physiotherapist treating a patient's knee in a clinic room with a wheelchair, exercise ball and plant"></div>

  <h2 class="tagline">
    <span class="light">EMPOWERING YOUR</span>
    <span class="bold">NEXT CAREER MOVE</span>
  </h2>

  <p class="discover">DISCOVER</p>
  <p class="intro">tailored opportunities based on your<br>career preferences</p>

  <ul class="sectors">
    <li class="sector">
      <svg viewBox="0 0 64 64" aria-hidden="true"><path d="M32 44 L14 27 a10 10 0 0 1 18-12 a10 10 0 0 1 18 12 Z" fill="#0a1485"/><path d="M8 54 h20 l14-6" stroke="#1f86ec" stroke-width="5" fill="none" stroke-linecap="round"/></svg>
      Allied health
    </li>
    <li class="sector">
      <svg viewBox="0 0 64 64" aria-hidden="true"><rect x="20" y="6" width="24" height="12" rx="3" fill="#0a1485"/><circle cx="32" cy="28" r="10" fill="#3242d8"/><path d="M12 62 a20 20 0 0 1 40 0 Z" fill="#0a1485"/></svg>
      Nursing
    </li>
    <li class="sector">
      <svg viewBox="0 0 64 64" aria-hidden="true"><path d="M50 20 A20 20 0 1 0 50 44" stroke="#1f86ec" stroke-width="8" fill="none"/><rect x="20" y="30" width="38" height="8" fill="#262626"/></svg>
      Medical imaging
    </li>
  </ul>

  <div class="web">www.quellastaffing.com.au</div>

  <p class="social"><span class="light">Follow us at</span><span class="dot"></span><span class="handle">@quellastaffing</span></p>
</main>
</body>
</html>
```